Business Card for Industrial Distributor

We need a business card design for an industrial distributor. We sell machine parts for the manufacturing and oil industry. We would like the cards to look clean and modern but with a touch of industry.

Our colors are blue/white.

Please feel free to visit our website www.korvelpartsco.com

Target Market(s)

mexican manufacturers in the automobile/aerospace industry

Industry/Entity Type

Industrial

Colors
ffffff
0555a3

```html
<!DOCTYPE html>
<html lang="en">
<head>
<meta charset="utf-8">
<title>Korvel Business Card</title>
<link rel="stylesheet" href="https://fonts.googleapis.com/css2?family=Open+Sans:wght@400;700;800&display=swap">
<style>
  :root {
    --page: #e9ebef;
    --white: #ffffff;
    --brand-navy: #27349a;
    --brand-blue: #0555a3;
    --card-deep: #2a4ea3;
    --card-bright: #1f76c4;
    --accent-soft: #3d8fd6;
    --band: #2f6fc9;
    --text-light: #ffffff;
  }
  * { box-sizing: border-box; margin: 0; padding: 0; }
  html, body {
    width: 1200px; height: 900px; overflow: hidden;
    background: var(--page);
    font-family: "Open Sans", sans-serif;
  }
  .stage {
    position: relative; width: 1200px; height: 900px;
  }
  .card {
    position: absolute; width: 560px; height: 320px;
    border-radius: 4px; overflow: hidden;
    box-shadow: 0 8px 24px rgba(0,0,0,0.15);
  }
  .card-front {
    left: 40px; top: 290px; background: var(--white);
    display: flex; align-items: center; justify-content: center; gap: 18px;
  }
  .brand-dot {
    width: 78px; height: 78px; border-radius: 50%;
    background: var(--brand-blue);
  }
  .brand-name {
    font-weight: 800; font-size: 86px; color: var(--brand-navy);
    letter-spacing: -1px; line-height: 1;
  }
  .card-back {
    left: 620px; top: 290px;
    background: linear-gradient(135deg, var(--card-deep) 0%, var(--card-deep) 55%, var(--card-bright) 100%);
    color: var(--text-light);
  }
  .back-decor {
    position: absolute; right: -150px; top: -250px;
    width: 420px; height: 420px; border-radius: 50%;
    background: var(--accent-soft); opacity: 0.55;
  }
  .back-band {
    position: absolute; left: 0; right: 0; bottom: 0; height: 14px;
    background: var(--band);
  }
  .person { position: absolute; left: 40px; top: 56px; }
  .person-name { font-size: 30px; font-weight: 400; line-height: 1.1; }
  .person-role { font-size: 15px; font-weight: 700; margin-left: 14px; margin-top: 2px; }
  .contact-list { position: absolute; left: 52px; list-style: none; }
  .contact-list li {
    display: flex; align-items: center; gap: 8px;
    font-size: 17px; line-height: 24px;
  }
  .contact-list svg { width: 12px; height: 12px; fill: var(--text-light); flex: none; }
  .contact-phones { top: 142px; }
  .contact-web { top: 206px; }
  .address {
    position: absolute; left: 40px; bottom: 30px;
    font-size: 14px;
  }
</style>
</head>
<body>
<main class="stage">
  <section class="card card-front" aria-label="Card front">
    <span class="brand-dot"></span>
    <span class="brand-name">Korvel</span>
  </section>

  <section class="card card-back" aria-label="Card back">
    <div class="back-decor"></div>
    <div class="back-band"></div>

    <div class="person">
      <p class="person-name">Dana Whitlock</p>
      <p class="person-role">Administrator</p>
    </div>

    <ul class="contact-list contact-phones">
      <li>
        <svg viewBox="0 0 12 12"><path d="M1 4c0-2 2-3 5-3s5 1 5 3l-2 1-1-2H4L3 5zM3 6h6l1 5H2z"/></svg>
        555-204-3180
      </li>
      <li>
        <svg viewBox="0 0 12 12"><path d="M3 0h6v12H3zM4 1.5v8h4v-8zM5.5 10.2h1v1h-1z" fill-rule="evenodd"/></svg>
        555-204-31927
      </li>
    </ul>

    <ul class="contact-list contact-web">
      <li>
        <svg viewBox="0 0 12 12"><path d="M0 2h12v8H0zM1 3l5 4 5-4z" fill-rule="evenodd"/></svg>
        info@korvelparts.com
      </li>
      <li>
        <svg viewBox="0 0 12 12"><circle cx="6" cy="6" r="6"/><path d="M3 4l2 1 1 3-2 1zM7 2l3 2-1 2-2-1z" fill="#2a4ea3"/></svg>
        www.korvelpartsco.com
      </li>
    </ul>

    <p class="address">48 W. Harlow Suite 910 Fairmont, Ohio 45201</p>
  </section>
</main>
</body>
</html>
```